Clean business card with logo provided

I want a card that will stand out among the masses. I need the color and image to show professionalism and yet have a family appeal showing that I only deal with win/win scenarios. The back of the card will be used to take notes about the individual so I can use that in my database entry. I like modern design but need professionalism in it also. It needs to fit my "clean, safe, and affordable housing" motto. I need to be able to write on the file and update the card details for my employees.

Target Market(s)

Investors looking to make investment income through real estate

Industry/Entity Type

Real Estate

Contact Information for Business Card

Brent Kovalich
blank address, city, st, zip code
480-555-3174
brentkovalich@ridgeworthrentals.example
www.ridgeworthrentals.example

Font styles to use
Sans Serif

Requirements
Must have
• I would like the back of the card to have lines for info. example
• Met/Visited: Date:
• Interets:
Nice to have
• I want the cards color to match the logo background color. Font with details to be san serif and black. I want the card rectangular with square corners. Standard business card size. I would like to see cards designed with both images to see which i prefer more.

```html
<!DOCTYPE html>
<html lang="en">
<head>
<meta charset="utf-8">
<title>Ridgeworth Rentals LLC – Business Card</title>
<link rel="stylesheet" href="https://fonts.googleapis.com/css2?family=Open+Sans:wght@400;600;700&display=swap">
<style>
  :root {
    --teal: #19b3cc;
    --teal-dark: #1497ad;
    --ink: #1b1b1b;
    --paper: #ffffff;
    --backdrop: #e9ecee;
    --rule: #2a2a2a;
  }
  * { box-sizing: border-box; margin: 0; padding: 0; }
  html, body { width: 1200px; height: 900px; overflow: hidden; }
  body {
    background: var(--backdrop);
    font-family: "Open Sans", Arial, sans-serif;
    color: var(--ink);
    position: relative;
  }
  .card {
    position: absolute;
    width: 700px;
    height: 400px;
    border-radius: 14px;
    overflow: hidden;
    box-shadow: 0 10px 28px rgba(0,0,0,.18);
  }
  .card-back { left: 60px; top: 45px; background: var(--paper); }
  .card-front { left: 440px; top: 460px; background: var(--teal); }
  .card svg.shapes { position: absolute; inset: 0; }

  /* brand lockup */
  .brand { position: absolute; display: flex; flex-direction: column; }
  .brand-row { display: flex; align-items: center; gap: 10px; }
  .brand-mark { width: 13px; height: 13px; flex: none; }
  .brand-name {
    font-weight: 600;
    font-size: 22px;
    letter-spacing: 2px;
    line-height: 1;
    white-space: nowrap;
  }
  .brand-motto { font-size: 12px; font-weight: 600; margin-top: 6px; padding-left: 23px; white-space: nowrap; }

  /* back side */
  .card-back .brand { left: 230px; top: 60px; }
  .card-back .brand-mark { background: var(--teal); }
  .card-back .brand-name, .card-back .brand-motto { color: var(--teal); }
  .notes-title {
    position: absolute; left: 60px; top: 182px;
    color: var(--teal); font-weight: 700; font-size: 20px;
  }
  .note-line {
    position: absolute; left: 60px; width: 580px;
    display: flex; align-items: flex-end; font-size: 17px;
  }
  .note-line span { white-space: nowrap; }
  .note-line i {
    flex: 1; border-bottom: 1.5px dashed var(--rule);
    margin-left: 4px; margin-bottom: 5px;
  }
  .note-name { top: 225px; }
  .note-date { top: 270px; }
  .note-interests { top: 315px; }

  /* front side */
  .card-front .brand { left: 55px; top: 97px; }
  .card-front .brand-mark { background: var(--paper); }
  .card-front .brand-name, .card-front .brand-motto { color: var(--paper); }
  .address {
    position: absolute; right: 40px; top: 124px;
    text-align: right; font-size: 16px; font-style: normal;
    line-height: 1.35; color: var(--ink);
  }
  .holder {
    position: absolute; left: 70px; top: 225px;
    font-size: 27px; font-weight: 700; letter-spacing: .5px;
  }
  .holder .first { color: var(--ink); }
  .holder .last { color: var(--paper); }
  .contacts {
    position: absolute; left: 70px; top: 283px;
    list-style: none; font-size: 16px; line-height: 1.45;
  }
  .contacts li { display: flex; align-items: center; gap: 12px; }
  .contacts svg { width: 14px; height: 14px; flex: none; }
</style>
</head>
<body>

<section class="card card-back" aria-label="Card back: notes">
  <svg class="shapes" width="700" height="400" aria-hidden="true">
    <polygon points="0,364 300,364 335,378 335,400 0,400" fill="var(--teal)"/>
  </svg>
  <div class="brand">
    <div class="brand-row"><span class="brand-mark"></span><span class="brand-name">RIDGEWORTH RENTALS LLC</span></div>
    <p class="brand-motto">Providing clean, safe, and affordable housing</p>
  </div>
  <h2 class="notes-title">Met/Visited:</h2>
  <div class="note-line note-name"><span>Name:</span><i></i></div>
  <div class="note-line note-date"><span>Date:</span><i></i></div>
  <div class="note-line note-interests"><span>Interets:</span><i></i></div>
</section>

<section class="card card-front" aria-label="Card front: contact">
  <svg class="shapes" width="700" height="400" aria-hidden="true">
    <line x1="478" y1="108" x2="665" y2="108" stroke="var(--rule)" stroke-width="1.2"/>
    <line x1="70" y1="268" x2="445" y2="268" stroke="var(--rule)" stroke-width="1.2"/>
    <polygon points="445,358 700,358 700,400 455,400 455,372" fill="var(--paper)"/>
  </svg>
  <div class="brand">
    <div class="brand-row"><span class="brand-mark"></span><span class="brand-name">RIDGEWORTH RENTALS LLC</span></div>
    <p class="brand-motto">Providing clean, safe, and affordable housing</p>
  </div>
  <address class="address">2874 Harbor Avenue<br>Millbrook Falls, OH 44390</address>
  <h1 class="holder"><span class="first">BRENT</span> <span class="last">KOVALICH</span></h1>
  <ul class="contacts">
    <li>
      <svg viewBox="0 0 24 24" aria-hidden="true"><path fill="var(--paper)" d="M6.6 10.8a15 15 0 0 0 6.6 6.6l2.2-2.2a1 1 0 0 1 1-.25 11.4 11.4 0 0 0 3.6.57 1 1 0 0 1 1 1V20a1 1 0 0 1-1 1A17 17 0 0 1 3 4a1 1 0 0 1 1-1h3.5a1 1 0 0 1 1 1c0 1.25.2 2.45.57 3.57a1 1 0 0 1-.25 1z"/></svg>
      480-555-3174
    </li>
    <li>
      <svg viewBox="0 0 24 24" aria-hidden="true"><rect x="3" y="5" width="18" height="14" rx="1.5" fill="none" stroke="var(--paper)" stroke-width="2"/><path d="M3 6l9 7 9-7" fill="none" stroke="var(--paper)" stroke-width="2"/></svg>
      brentkovalich@ridgeworthrentals.example
    </li>
    <li>
      <svg viewBox="0 0 24 24" aria-hidden="true"><circle cx="12" cy="12" r="9" fill="none" stroke="var(--paper)" stroke-width="2"/><path d="M3 12h18M12 3c3 3 3 15 0 18M12 3c-3 3-3 15 0 18" fill="none" stroke="var(--paper)" stroke-width="1.6"/></svg>
      www.ridgeworthrentals.example
    </li>
  </ul>
</section>

</body>
</html>
```